Business Card Design For Marketing Agnecy LVP

Need business card design for marketing agency.

Doug Fenwick
President, CEO
1-555-302-4196
doug@boldpromoperksgroup.example
www.BoldPromoPerksGroup.example

Back Side:
Boost Sales Using Rewards, Incentives & Giveaways
Get A Free Sample Package

Target Market(s)

B2B

Industry/Entity Type

Marketing

Contact Information for Business Card

Doug Fenwick
President, CEO
1-555-302-4196

Back Side:
Get A Free Sample Package

Please note that my current url is OLD DESIGN. I am working on new design and want the business card to match color themes at least on new site. Here is the demo link for new site so you can see the colors I use, etc.

http://layoutcratehub.example/kq/doug/lvp_final/index.html

Requirements
Must have
• Please note that my current url is OLD DESIGN. I am working on new design and want the business card to match color themes at least on new site. Here is the demo link for new site so you can see the colors I use, etc.

Nice to have

Should not have

```html
<!DOCTYPE html>
<html lang="en">
<head>
<meta charset="utf-8">
<title>LVP Business Card</title>
<link rel="stylesheet" href="https://fonts.googleapis.com/css2?family=Roboto:wght@400;700&family=Saira+Condensed:wght@600&display=swap">
<style>
  :root {
    --backdrop: #c0c0c0;
    --brand-blue: #3063a5;
    --ink-grey: #4a4a4c;
    --paper: #ffffff;
  }
  * { margin: 0; padding: 0; box-sizing: border-box; }
  html, body { width: 1200px; height: 1200px; overflow: hidden; }
  body { background: var(--backdrop); position: relative; font-family: "Roboto", Arial, sans-serif; }

  .card {
    position: absolute;
    left: 186px;
    width: 826px;
    height: 499px;
  }
  .card--back { top: 82px; background: var(--brand-blue); color: var(--paper); }
  .card--front { top: 618px; background: var(--paper); }

  .brand {
    position: absolute;
    display: flex;
    flex-direction: column;
    align-items: center;
    font-weight: 700;
  }
  .brand__mark { line-height: 0.8; letter-spacing: 1px; }
  .brand__name { letter-spacing: 1.5px; text-transform: uppercase; white-space: nowrap; }

  .card--back .brand { left: 262px; width: 302px; top: 84px; color: var(--paper); }
  .card--back .brand__mark { font-size: 175px; }
  .card--back .brand__name { font-size: 20px; margin-top: 30px; }

  .card--front .brand { left: 70px; width: 242px; top: 160px; color: var(--brand-blue); }
  .card--front .brand__mark { font-size: 135px; }
  .card--front .brand__name { font-size: 16px; margin-top: 22px; }

  .tagline {
    position: absolute;
    top: 360px;
    left: 0;
    width: 100%;
    text-align: center;
    font-size: 21px;
    line-height: 31px;
  }

  .person { position: absolute; left: 368px; top: 150px; }
  .person__name {
    font-family: "Saira Condensed", "Arial Narrow", sans-serif;
    font-weight: 600;
    font-size: 36px;
    line-height: 1;
    color: var(--brand-blue);
  }
  .person__title { font-size: 20px; color: var(--ink-grey); margin-top: 6px; }

  .contacts { position: absolute; left: 368px; top: 255px; list-style: none; }
  .contacts li {
    display: flex;
    align-items: center;
    height: 31px;
    font-size: 21px;
    color: var(--ink-grey);
  }
  .contacts svg { width: 20px; height: 20px; margin-right: 16px; fill: var(--brand-blue); flex: none; }
</style>
</head>
<body>

<section class="card card--back">
  <div class="brand">
    <span class="brand__mark">LVP</span>
    <span class="brand__name">Bold Promo Perks Group</span>
  </div>
  <p class="tagline">
    Boost Sales Using Rewards, Incentives &amp; Giveaways<br>
    Get A Free Sample Package<br>
    www.BoldPromoPerksGroup.example
  </p>
</section>

<section class="card card--front">
  <div class="brand">
    <span class="brand__mark">LVP</span>
    <span class="brand__name">Bold Promo Perks Group</span>
  </div>

  <div class="person">
    <h1 class="person__name">Doug Fenwick</h1>
    <p class="person__title">President, CEO</p>
  </div>

  <ul class="contacts">
    <li>
      <svg viewBox="0 0 20 20" aria-hidden="true"><path d="M2 7c0-3 4-4 8-4s8 1 8 4v1h-4V6.5c-1-.5-2.5-.7-4-.7s-3 .2-4 .7V8H2z"/><path d="M5 9h10l2 8H3z"/><rect x="8" y="11" width="4" height="4" fill="#fff"/></svg>
      1-555-302-4196
    </li>
    <li>
      <svg viewBox="0 0 20 20" aria-hidden="true"><path d="M1 4h18v12H1z"/><path d="M1.5 4.5 10 11l8.5-6.5M1.5 15.5l6-5.5m11 5.5-6-5.5" stroke="#fff" stroke-width="1.4" fill="none"/></svg>
      doug@boldpromoperksgroup.example
    </li>
    <li>
      <svg viewBox="0 0 20 20" aria-hidden="true"><circle cx="10" cy="10" r="9"/><g stroke="#fff" stroke-width="1.1" fill="none"><ellipse cx="10" cy="10" rx="4" ry="9"/><path d="M1 10h18M2.5 5.5h15M2.5 14.5h15M10 1v18"/></g></svg>
      www.BoldPromoPerksGroup.example
    </li>
  </ul>
</section>

</body>
</html>
```